Web Developer Needs a Business Card Design

I need a personal business card design that represents me as a web developer for potential employers. I would like the background to be a dark color on the front for contrast with my logo and name. The back will have all my information along with a smaller version of the logo. I want something with a modern look and feel, not too conservative. This will be used for potential employers and freelance work.

Industry/Entity Type

Business

Contact Information for Business Card

Front should have my logo and name. The back should have all my personal information which would include: name: Tom Varulek, phone: 570-614-3098, email: tomvarulek@quillbox.net, website url: www.tomvarulek.net, logo, web developer.

Font styles to use
Sans Serif

Requirements
Must have
• Must include my logo. The color palette base color will be the logo color.

```html
<!DOCTYPE html>
<html lang="en">
<head>
<meta charset="utf-8">
<title>Tom Varulek – Business Card</title>
<link rel="stylesheet" href="https://fonts.googleapis.com/css2?family=Questrial&display=swap">
<style>
  :root {
    --backdrop: #8a8b8a;
    --card-paper: #e6e6e5;
    --brand-teal: #4fc9ad;
    --ink-black: #161616;
    --ink-dark: #2b2b2b;
    --text-light: #d6d6d6;
  }
  html, body {
    margin: 0;
    padding: 0;
    width: 1200px;
    height: 900px;
    overflow: hidden;
    background: var(--backdrop);
    font-family: "Questrial", "Century Gothic", sans-serif;
  }
  .canvas {
    position: relative;
    width: 1200px;
    height: 900px;
  }
  .card {
    position: absolute;
    left: 347px;
    width: 507px;
    height: 290px;
    display: block;
  }
  .card--front { top: 119px; }
  .card--back { top: 471px; }
  .card-text { font-family: "Questrial", "Century Gothic", sans-serif; }
  .brand-name { fill: var(--brand-teal); }
  .holder-name { fill: var(--brand-teal); font-size: 26px; }
  .holder-role { fill: var(--text-light); font-size: 16px; }
  .contact-line { fill: var(--text-light); font-size: 14px; }
</style>
</head>
<body>
<main class="canvas">

  <!-- Front side: brand mark and social row -->
  <svg class="card card--front" viewBox="0 0 541 309" role="group" aria-label="Card front">
    <rect class="card-surface" width="541" height="309" fill="var(--card-paper)"/>
    <g class="brand-lockup">
      <circle cx="270" cy="150" r="18" fill="none" stroke="var(--brand-teal)" stroke-width="4"/>
      <text class="card-text brand-name" x="270" y="205" font-size="26" text-anchor="middle">Tom Varulek</text>
    </g>
    <g class="social-row">
      <line x1="80" y1="265" x2="220" y2="265" stroke="var(--brand-teal)" stroke-width="1" opacity="0.7"/>
      <line x1="318" y1="265" x2="458" y2="265" stroke="var(--brand-teal)" stroke-width="1" opacity="0.7"/>
      <circle cx="239" cy="265" r="11" fill="none" stroke="var(--ink-dark)" stroke-width="2.5"/>
      <circle cx="268" cy="265" r="11" fill="none" stroke="var(--ink-dark)" stroke-width="2.5"/>
      <circle cx="297" cy="265" r="11" fill="none" stroke="var(--ink-dark)" stroke-width="2.5"/>
    </g>
  </svg>

  <!-- Back side: wave, details -->
  <svg class="card card--back" viewBox="0 0 541 309" role="group" aria-label="Card back">
    <rect class="card-surface" width="541" height="309" fill="var(--card-paper)"/>
    <path class="wave-panel" fill="var(--ink-black)"
          d="M0,212 C60,262 150,282 240,228 C330,172 380,58 470,50 L541,48 L541,309 L0,309 Z"/>
    <path class="wave-accent" fill="none" stroke="var(--card-paper)" stroke-width="12"
          d="M0,196 C60,246 150,268 230,222 C270,198 288,172 300,150"/>
    <path class="wave-accent" fill="none" stroke="var(--brand-teal)" stroke-width="8" stroke-linecap="round"
          d="M0,196 C60,246 150,266 228,220 C266,197 284,172 298,152"/>
    <polygon class="wave-arrowhead" fill="var(--brand-teal)" points="310,140 292,146 302,156"/>

    <g class="brand-lockup">
      <circle cx="113" cy="90" r="18" fill="none" stroke="var(--brand-teal)" stroke-width="4"/>
      <text class="card-text brand-name" x="113" y="145" font-size="26" text-anchor="middle">Tom Varulek</text>
    </g>

    <text class="card-text holder-name" x="508" y="168" text-anchor="end">Tom Varulek</text>
    <text class="card-text holder-role" x="508" y="191" text-anchor="end">Web Developer</text>

    <g class="contact-list">
      <text class="card-text contact-line" x="480" y="233" text-anchor="end">570-614-3098</text>
      <text class="card-text contact-line" x="480" y="256" text-anchor="end">tomvarulek@quillbox.net</text>
      <text class="card-text contact-line" x="480" y="278" text-anchor="end">www.tomvarulek.net</text>

      <path class="icon-phone" fill="var(--brand-teal)"
            d="M493,222 l3,-1 l2,4 l-2,2 q1,3 4,4 l2,-2 l4,2 l-1,3 q-9,1 -12,-12 z"/>
      <g class="icon-mail">
        <rect x="491" y="248" width="13" height="9" fill="var(--brand-teal)"/>
        <polyline points="491,248 497.5,253 504,248" fill="none" stroke="var(--ink-black)" stroke-width="1.2"/>
      </g>
      <g class="icon-web">
        <circle cx="498" cy="274" r="6.5" fill="var(--brand-teal)"/>
        <ellipse cx="498" cy="274" rx="2.6" ry="6.5" fill="none" stroke="var(--ink-black)" stroke-width="1"/>
        <line x1="491.5" y1="274" x2="504.5" y2="274" stroke="var(--ink-black)" stroke-width="1"/>
      </g>
    </g>
  </svg>

</main>
</body>
</html>
```